Oil and Gas Exploration and Production company needs a business card design

We need a business card design using our logo and colors in the logo. We want a mainstream design.

```html
<!DOCTYPE html>
<html lang="en">
<head>
<meta charset="utf-8">
<title>Andor Oil &amp; Gas – Business Card</title>
<link rel="stylesheet" href="https://fonts.googleapis.com/css2?family=Open+Sans:wght@400;600;700;800&display=swap">
<style>
  :root {
    --page-bg: #e4e4e4;
    --gold-light: #ead44c;
    --gold-mid: #d6ab35;
    --gold-deep: #c8962d;
    --band-gold: #c89a2e;
    --ink: #1b1b1b;
    --text-grey: #5a5a5a;
    --paper: #f4f4f4;
    --divider: #dadada;
    --white: #ffffff;
  }
  * { box-sizing: border-box; margin: 0; padding: 0; }
  html, body {
    width: 1200px; height: 900px; overflow: hidden;
    background: var(--page-bg);
    font-family: "Open Sans", Arial, sans-serif;
  }
  .canvas {
    width: 1200px; height: 900px;
    display: flex; flex-direction: column; align-items: center; justify-content: center;
    gap: 56px;
  }
  .card {
    width: 620px; height: 354px; position: relative; overflow: hidden;
    box-shadow: 0 8px 24px rgba(0,0,0,.18);
  }

  /* Front */
  .card-front {
    background: linear-gradient(100deg, var(--gold-light) 0%, var(--gold-mid) 45%, var(--gold-deep) 100%);
    display: flex; align-items: center; justify-content: center;
  }
  .brand { display: flex; align-items: center; gap: 14px; color: var(--ink); white-space: nowrap; }
  .brand-dot { width: 34px; height: 34px; border-radius: 50%; background: var(--ink); flex: none; }
  .brand-name { font-weight: 800; font-size: 46px; letter-spacing: .5px; line-height: 1; }

  /* Back */
  .card-back { background: var(--paper); }
  .card-back .brand {
    position: absolute; left: 0; width: 356px; top: 130px;
    justify-content: center; gap: 10px;
  }
  .card-back .brand-dot { width: 22px; height: 22px; }
  .card-back .brand-name { font-size: 25px; letter-spacing: .3px; }

  .contact {
    position: absolute; left: 356px; top: 26px; bottom: 110px;
    padding-left: 18px; border-left: 1px solid var(--divider);
  }
  .contact-name { font-weight: 800; font-size: 15px; color: var(--ink); letter-spacing: .3px; }
  .contact-title { font-weight: 600; font-size: 12px; color: var(--band-gold); margin-bottom: 6px; }
  .contact-address { font-size: 12px; color: var(--text-grey); line-height: 1.35; margin-bottom: 6px; }
  .contact-list { list-style: none; font-size: 12px; color: var(--text-grey); }
  .contact-list li { display: flex; align-items: center; gap: 8px; line-height: 1.45; }
  .contact-list svg { width: 11px; height: 11px; fill: var(--ink); flex: none; }

  .accent-strip {
    position: absolute; right: 0; top: 236px; width: 268px; height: 24px;
    background: var(--band-gold);
    display: flex; align-items: center; justify-content: flex-end; padding-right: 10px;
  }
  .accent-dot { width: 14px; height: 14px; border-radius: 50%; background: var(--ink); }

  .web-band {
    position: absolute; left: 0; right: 0; bottom: 0; height: 62px;
    background: var(--band-gold);
    display: flex; align-items: center; justify-content: center;
  }
  .web-address { color: var(--white); font-size: 14px; letter-spacing: 6px; }
</style>
</head>
<body>
<main class="canvas">
  <section class="card card-front" aria-label="Business card front">
    <div class="brand">
      <span class="brand-dot"></span>
      <span class="brand-name">Andor Oil &amp; Gas</span>
    </div>
  </section>

  <section class="card card-back" aria-label="Business card back">
    <div class="brand">
      <span class="brand-dot"></span>
      <span class="brand-name">Andor Oil &amp; Gas</span>
    </div>

    <div class="contact">
      <p class="contact-name">MARCUS HALE</p>
      <p class="contact-title">PRESIDENT</p>
      <p class="contact-address">2190 Harlow Avenue<br>Brookvale, NY 10542</p>
      <ul class="contact-list">
        <li>
          <svg viewBox="0 0 12 12" aria-hidden="true"><path d="M1 3c0-1 1-2 2-2h6c1 0 2 1 2 2v1H8V3H4v1H1zM2 5h8l1 6H1z"/></svg>
          555 0142 7781
        </li>
        <li>
          <svg viewBox="0 0 12 12" aria-hidden="true"><path d="M3 0h6v12H3zM4 1.5v8h4v-8z"/></svg>
          555 0187 3364
        </li>
        <li>
          <svg viewBox="0 0 12 12" aria-hidden="true"><path d="M3 0h6v4H3zM1 5h10v6H1zM3 7v1h6V7z"/></svg>
          555 0163 9042
        </li>
        <li>
          <svg viewBox="0 0 12 12" aria-hidden="true"><path d="M0 2h12v1L6 7 0 3zM0 4.5l6 4 6-4V10H0z"/></svg>
          info@andoroilgas.com
        </li>
      </ul>
    </div>

    <div class="accent-strip"><span class="accent-dot"></span></div>

    <div class="web-band">
      <span class="web-address">www.andoroilgas.com</span>
    </div>
  </section>
</main>
</body>
</html>
```